Simple and Clean business card design

We would like the design to be simple clean and to incorporate our colors.

We are open to your design and talent, we have the dots in our logo as we think of it as data points and we connect data points for people.

We are open to see the great creative and clean design you bring to the table

Contact Information for Business Card

please include: name, position, email, phone and website

Font styles to use
Sans Serif

Requirements
Must have
• my colors incorporated, simplicity
Nice to have
• lots of white space, simplicity
Should not have
• complexicity/ complex art

```html
<!DOCTYPE html>
<html lang="en">
<head>
<meta charset="utf-8">
<title>Meadow – Business Card</title>
<link rel="stylesheet" href="https://fonts.googleapis.com/css2?family=Montserrat:wght@500;600&family=Work+Sans:wght@400&display=swap">
<style>
  :root {
    --page-bg: #e9e6e1;
    --card-bg: #ffffff;
    --card-edge: #d9d6d0;
    --ink: #1f1f1f;
    --ink-soft: #2f2f2f;
    --brand-blue: #4a74c0;
    --brand-green: #1f8f3a;
    --brand-yellow: #e5b40c;
    --brand-red: #d2271b;
  }
  * { margin: 0; padding: 0; box-sizing: border-box; }
  html, body {
    width: 1200px;
    height: 887px;
    overflow: hidden;
    background: var(--page-bg);
  }
  .card {
    position: absolute;
    left: 100px;
    top: 170px;
    width: 1000px;
    height: 547px;
    background: var(--card-bg);
    border: 1px solid var(--card-edge);
    border-radius: 26px;
    box-shadow: 0 10px 30px rgba(0,0,0,0.08);
    overflow: hidden;
  }
  .brand-name {
    position: absolute;
    left: 60px;
    top: 62px;
    font-family: "Montserrat", sans-serif;
    font-weight: 600;
    font-size: 92px;
    line-height: 1;
    letter-spacing: -1px;
    color: var(--ink);
  }
  .accent-bar {
    position: absolute;
    left: 6px;
    top: 249px;
    width: 16px;
    height: 60px;
    background: var(--brand-yellow);
  }
  .person-name {
    position: absolute;
    left: 61px;
    top: 240px;
    font-family: "Montserrat", sans-serif;
    font-weight: 600;
    font-size: 36px;
    letter-spacing: 1.5px;
    color: var(--brand-blue);
  }
  .person-role {
    position: absolute;
    left: 61px;
    top: 284px;
    font-family: "Work Sans", sans-serif;
    font-size: 24px;
    color: var(--ink-soft);
    letter-spacing: 0.5px;
  }
  .address {
    position: absolute;
    left: 61px;
    top: 328px;
    font-family: "Work Sans", sans-serif;
    font-size: 24px;
    line-height: 33px;
    color: var(--ink-soft);
    font-style: normal;
    letter-spacing: 0.5px;
  }
  .contact-list {
    position: absolute;
    left: 58px;
    top: 406px;
    list-style: none;
    font-family: "Work Sans", sans-serif;
    font-size: 24px;
    line-height: 32px;
    color: var(--ink-soft);
    letter-spacing: 0.6px;
  }
  .contact-list li { display: flex; align-items: center; gap: 8px; }
  .contact-icon { width: 17px; height: 17px; flex: none; }
  .decor-dot {
    position: absolute;
    left: 560px;
    top: 150px;
  }
</style>
</head>
<body>
  <main class="card">
    <div class="brand-name">Meadow</div>

    <svg class="decor-dot" width="300" height="300" viewBox="0 0 300 300" aria-hidden="true">
      <circle cx="150" cy="150" r="108" fill="var(--brand-green)" opacity="0.9"/>
    </svg>

    <span class="accent-bar"></span>
    <h1 class="person-name">DANIEL REYES</h1>
    <p class="person-role">Founder</p>
    <address class="address">1470 Cedar Hollow Lane<br>Brookfield, TX 78012</address>

    <ul class="contact-list">
      <li>
        <svg class="contact-icon" viewBox="0 0 24 24" aria-hidden="true"><path d="M6.6 2.5l3 3.2-2 2.3c1.2 2.8 3.4 5 6.2 6.3l2.3-2 3.2 3-2 3.4C10 18 6 14 3.5 7.5L6.6 2.5z" fill="var(--ink-soft)"/></svg>
        <span>0455 218 903</span>
      </li>
      <li>
        <svg class="contact-icon" viewBox="0 0 24 24" aria-hidden="true"><rect x="2.5" y="5.5" width="19" height="13" rx="1.5" fill="none" stroke="var(--ink-soft)" stroke-width="2"/><path d="M3 6.5l9 6.5 9-6.5" fill="none" stroke="var(--ink-soft)" stroke-width="2"/></svg>
        <span>hello@brightnode.com</span>
      </li>
      <li>
        <svg class="contact-icon" viewBox="0 0 24 24" aria-hidden="true"><circle cx="12" cy="12" r="9" fill="none" stroke="var(--ink-soft)" stroke-width="1.8"/><ellipse cx="12" cy="12" rx="4" ry="9" fill="none" stroke="var(--ink-soft)" stroke-width="1.6"/><path d="M3 12h18M5 7.5h14M5 16.5h14" stroke="var(--ink-soft)" stroke-width="1.4"/></svg>
        <span>www.brightnode.com</span>
      </li>
    </ul>
  </main>
</body>
</html>
```